The logo name is "Harbor Skin". The name of the product will be "Cutaneous Comfort". This product is specifically formulated for amputees. Therefore under the product name it should state "for amputees". The catch phrase will be "Experience Harbor find Calmness"
These are the things we need on the label:
Logo, product name, "for amputees", "Experience Harbor find Calmness", Safe, Effective, Directions: spray on problem areas, no need to dry off. harborskin.example, Made in Canada, 500ml.
The MOST IMPORTANT and therefore the most prominent thing on this lable will be the LOGO! The second most prominent thing will be the word "Comfort" We want to keep it very plain, very simple, very unclutered. Keep in mind that this lable will be placed on a white bottle or have a white back ground. The 500ml white PE bottle with trigger sprayer will have a tear drop label. See attached die line (S-294).
We want to stay with the colours that goes with the colour scheme of the logo. See attached logo. Soft colours. We do not want a picture! We would like the lable to be classy and rich.
Updates
The logo name is "Harbor Skin". The name of the product will be "Cutaneous Comfort". This product is specificlly formulated for amputees. Therefore under the product name it should state "for amputees". The catch phrase will be "Experience Harbor find Calmness"
Logo, product name, "for amputees", catch phrase "Experience Harbor find Calmness", Clean, Safe, Effective, Directions: spray on problem areas, no need to dry off. Also Harbor Skin Corpation, harborskin.example, Made in Canada, 500ml.
We want to stay with the colour scheme of the logo. See attached logo. Soft colours. We do not want a picture! We would like the lable to be classy and rich.
This is the offical directive that came from the governing panal of this lable. This panal it not know where it wanted to take this lable that would represent this line until they review all of your submissions, thank you for all your talented hard work. But now it is clear it is time to regroup and hit this objective.
Project Deadline Extended
Reason: New restrictions on lable wording for this product.
Target Market(s)
Amputees and Parents of.
Industry/Entity Type
Product
Requirements
Must have
- Final product to be in a pdf or an illustrator file

```html
<!DOCTYPE html>
<html lang="en">
<head>
<meta charset="utf-8">
<title>Harbor Skin – Cutaneous Comfort Label</title>
<link rel="stylesheet" href="https://fonts.googleapis.com/css2?family=Questrial&family=Lato:wght@400;700&family=Roboto+Slab:wght@700&display=swap">
<style>
  :root {
    --page: #ffffff;
    --lavender: #a69ffb;
    --mint: #8efca8;
    --ice: #e6f4fb;
    --amber: #f7b12b;
    --amber-soft: #f9c45a;
    --forest: #1e5a2b;
    --ink-light: #ffffff;
    --ink-mist: #eef0ff;
  }
  * { margin: 0; padding: 0; box-sizing: border-box; }
  html, body {
    width: 1200px; height: 900px; overflow: hidden;
    background: var(--page);
  }
  .canvas { position: relative; width: 1200px; height: 900px; }
  .label-shape { position: absolute; inset: 0; }
  .label-text { position: absolute; white-space: nowrap; color: var(--ink-light); font-family: "Questrial", sans-serif; }

  .volume { left: 484px; top: 176px; font-size: 29px; }
  .origin { left: 486px; top: 212px; font-size: 13px; font-family: "Lato", sans-serif; }
  .claims { left: 461px; top: 367px; font-size: 23px; letter-spacing: 0.4px; }

  .brand { left: 462px; top: 414px; display: flex; align-items: center; gap: 12px; max-width: 270px; }
  .brand-mark { width: 70px; height: 70px; flex: none; background: var(--mint); }
  .brand-name { font-family: "Questrial", sans-serif; font-size: 35px; color: var(--forest); }

  .product-line { left: 459px; top: 508px; font-size: 31px; color: var(--ink-mist); }
  .product-hero { left: 456px; top: 546px; font-size: 76px; color: var(--amber); line-height: 1; letter-spacing: -1px; }
  .audience { left: 459px; top: 624px; font-size: 20px; font-family: "Roboto Slab", serif; font-weight: 700; color: var(--ink-mist); }

  .directions { left: 459px; top: 656px; font-family: "Lato", sans-serif; font-size: 14px; line-height: 18px; color: var(--ink-mist); }
  .directions-title { font-weight: 700; font-size: 13px; }

  .tagline { left: 463px; top: 779px; font-size: 18px; }
  .maker { left: 465px; top: 806px; font-size: 13px; font-family: "Lato", sans-serif; }
</style>
</head>
<body>
<main class="canvas">
  <svg class="label-shape" width="1200" height="900" viewBox="0 0 1200 900">
    <defs>
      <clipPath id="teardrop-clip">
        <path d="M540 38 C590 30 700 200 800 380 C860 490 880 620 862 720 C848 790 825 832 800 833 L462 833 C440 833 425 780 420 700 C412 520 440 300 490 140 C505 90 520 40 540 38 Z"/>
      </clipPath>
    </defs>
    <path class="teardrop" fill="var(--lavender)" d="M540 38 C590 30 700 200 800 380 C860 490 880 620 862 720 C848 790 825 832 800 833 L462 833 C440 833 425 780 420 700 C412 520 440 300 490 140 C505 90 520 40 540 38 Z"/>
    <g clip-path="url(#teardrop-clip)">
      <path class="sweep-light" fill="var(--ice)" d="M503 96 C630 150 745 270 790 410 C818 510 828 660 822 840 L780 840 C790 660 778 520 740 420 C690 300 610 200 500 124 Z"/>
      <path class="sweep-mint" fill="var(--mint)" d="M498 112 C610 165 705 280 755 410 C792 520 806 660 810 840 L768 840 C776 680 770 530 735 430 C690 310 610 215 498 128 Z"/>
    </g>
    <ellipse class="grass-accent" role="img" aria-label="Soft amber grass sprig decoration" cx="770" cy="405" rx="30" ry="58" fill="var(--amber-soft)" opacity="0.75"/>
  </svg>

  <div class="label-text volume">500ml</div>
  <div class="label-text origin">made in Canada</div>
  <div class="label-text claims">Clean . Safe . Effective</div>

  <div class="label-text brand">
    <span class="brand-mark"></span>
    <span class="brand-name">Harbor Skin</span>
  </div>

  <div class="label-text product-line">Cutaneous</div>
  <div class="label-text product-hero">Comfort</div>
  <div class="label-text audience">For Amputees</div>

  <div class="label-text directions">
    <div class="directions-title">Directions</div>
    <div>Spray on problem areas,</div>
    <div>no need to dry off.</div>
  </div>

  <div class="label-text tagline">Experience Harbor, Find Calmness</div>
  <div class="label-text maker">Harbor Skin Corporation, harborskin.example</div>
</main>
</body>
</html>
```